Brochure and Business Card design

I am looking for a high end, elegant A4, 4 page brochure booklet to convey our products to clientele that will be visiting a luxury display showroom.

Harrowgate Locks and Grilles is a Australian security provider, and we supply high end products from reputable brands.
The brochure will be directed to clients building a new home with a partnered building company and will be accompanied with display boards of our products.

I am providing files of a document we have put together with the relevant information and some images to help along the way, we are not bound by the layout or style it has been drawn up and we wish to give you complete creative freedom putting the peaces together. I have also provided the files for our logo in two different colours, and a picture of a brochure we love the look of.

If you have any suggestions, we can likely come up with further images etc if it will help or even if you feel some should be removed, we are open to that also

Target Market(s)

Young familys, people building new luxury homes, proffesionals, home owners

Industry/Entity Type

Business

Font styles to use
Serif
Sans Serif

Requirements
Must have
• All 8 pages
Should not have
• Not really a fan of reds and similar.

```html
<!DOCTYPE html>
<html lang="en">
<head>
<meta charset="utf-8">
<title>Harrowgate Locks and Grilles – Alarm Systems &amp; Intercom</title>
<link href="https://fonts.googleapis.com/css2?family=Raleway:wght@300;400;600;700&family=Questrial&display=swap" rel="stylesheet">
<style>
  :root{
    --backdrop:#b3b3b3;
    --paper:#fafafa;
    --blue:#2a7fc1;
    --green:#8dc43f;
    --ink:#555a5e;
    --ink-dark:#3d4246;
    --rule:#c9cccf;
    --tile-border:#e4e6e8;
    --photo-dark:#4a4a4a;
    --photo-light:#e2e4e6;
  }
  *{margin:0;padding:0;box-sizing:border-box}
  html,body{width:1200px;height:576px;overflow:hidden;background:var(--backdrop)}
  body{position:relative;font-family:"Questrial",sans-serif;color:var(--ink)}
  .spread{position:absolute;left:76px;top:86px;width:1046px;height:404px;background:var(--paper)}
  .abs{position:absolute}
  .page-title{font-family:"Raleway",sans-serif;font-weight:300;font-size:31px;color:var(--blue);letter-spacing:.2px;line-height:1}
  .body-copy{font-size:6.4px;line-height:8.1px;text-align:justify;color:var(--ink)}
  .body-copy p+p{margin-top:8px}
  .sub-head{font-family:"Raleway",sans-serif;font-weight:700;font-size:11px;color:var(--green)}
  .section-label{font-family:"Raleway",sans-serif;font-weight:700;font-size:10.5px;color:var(--green);letter-spacing:.3px}
  .cta{background:var(--blue);color:#fff;font-family:"Raleway",sans-serif;font-weight:700;font-size:8.6px;display:flex;align-items:center;padding-left:10px}
  .tile{background:#fff;border:1px solid var(--tile-border);display:flex;align-items:center;gap:8px;padding:0 8px}
  .tile-photo{flex:none;width:38px;height:38px;background:linear-gradient(135deg,#eef0f2,#c9ced3);border-radius:2px}
  .tile-label{font-family:"Raleway",sans-serif;font-weight:600;font-size:6.2px;line-height:7.6px;color:var(--ink-dark)}
  .upgrade-tile{flex-direction:row;padding:0 10px;gap:12px}
  .upgrade-tile .tile-photo{width:44px;height:50px}
  .product-photo{background:linear-gradient(135deg,#f0f1f2,#c3b79e 60%,#9aa3ab)}
  .product-name{font-family:"Raleway",sans-serif;font-weight:600;font-size:10px;color:var(--blue)}
  .product-copy{font-size:6.2px;line-height:7.7px;text-align:justify}
  .divider{height:1px;background:var(--rule)}
  .fold{position:absolute;left:522px;top:0;width:1px;height:404px;background:linear-gradient(var(--tile-border),transparent)}
</style>
</head>
<body>
<main class="spread">

  <!-- Alarm Systems page -->
  <section class="alarm-page">
    <div class="abs" role="img" aria-label="Soft faded interior wall behind header" style="left:180px;top:0;width:80px;height:86px;background:linear-gradient(90deg,var(--paper),#ececec)"></div>
    <div class="abs" role="img" aria-label="Alarm keypad mounted on a dark wall beside a door frame" style="left:254px;top:0;width:268px;height:86px;background:linear-gradient(90deg,#8a8a8a,var(--photo-dark) 45%,#3a3a3a 80%,#6d6760)"></div>

    <h1 class="abs page-title" style="left:26px;top:48px">Alarm Systems</h1>

    <div class="abs body-copy" style="left:26px;top:94px;width:196px">
      <p>A Harrowgate Locks and Grilles alarm system with its state of the art equipment is the perfect defense for your family and home. With detection devices such as motion detectors, magnetic door sensors and warning devices like siren + strobe combos to alert others of a break in to name a few, it will be everything you need to feel secure.</p>
      <p>With the added option of having your security system monitored, you will always have someone watching over your home, even when even when the house is vacant..</p>
      <p>Did you know, industry leaders say that burglars are 3 times more likely to to target a home without a security system. This means that simply having a home security system always keeps you safer, even if an alarm is never triggered.</p>
    </div>

    <h2 class="abs sub-head" style="left:255px;top:96px">Home Kits</h2>
    <p class="abs body-copy" style="left:255px;top:120px;width:255px;text-align:left">Standard kits consisting of everything you need to get an alarm up and running. Components such as an Alarm Control Panel, Keypad, 3 motion detectors, and internal siren, an external siren+strobe combo, battery back up incase the power goes out. A great starting platform that can be built on to your needs and requirements.</p>
    <div class="abs cta" style="left:255px;top:171px;width:252px;height:31px">Request a Security Advisor consultation&nbsp; for all the info.</div>

    <h3 class="abs section-label" style="left:26px;top:239px">POPULAR UPGRADES</h3>

    <div class="abs tile" style="left:26px;top:263px;width:112px;height:50px"><div class="tile-photo" role="img" aria-label="OLED keypad"></div><span class="tile-label">OLED&nbsp; Keypad<br>upgrade</span></div>
    <div class="abs tile" style="left:152px;top:263px;width:112px;height:50px"><div class="tile-photo" role="img" aria-label="Remote fobs and receiver board"></div><span class="tile-label">Remote Arm<br>and Disarm</span></div>
    <div class="abs tile" style="left:273px;top:263px;width:112px;height:50px"><div class="tile-photo" role="img" aria-label="Dome motion detector"></div><span class="tile-label">360 degree<br>motion detectors</span></div>
    <div class="abs tile" style="left:399px;top:263px;width:112px;height:50px"><div class="tile-photo" role="img" aria-label="Magnetic reed switch"></div><span class="tile-label">Door and window<br>magnetic switches</span></div>

    <div class="abs tile" style="left:26px;top:321px;width:112px;height:50px"><div class="tile-photo" role="img" aria-label="Monitoring communicator unit"></div><span class="tile-label">Professional<br>Alarm Monitoring</span></div>
    <div class="abs tile" style="left:152px;top:321px;width:112px;height:50px"><div class="tile-photo" role="img" aria-label="Wall motion detector"></div><span class="tile-label">Motion Detectors'<br>in additional<br>rooms</span></div>
    <div class="abs tile" style="left:273px;top:321px;width:112px;height:50px"><div class="tile-photo" role="img" aria-label="Roller door magnetic switch"></div><span class="tile-label">Roller door<br>magnetic switch</span></div>
  </section>

  <div class="fold"></div>

  <!-- Intercom page -->
  <section class="intercom-page">
    <div class="abs" role="img" aria-label="Front gate and garden path in soft light" style="left:748px;top:0;width:112px;height:86px;background:linear-gradient(90deg,var(--paper),#d5d9d6 40%,#a9aeaa)"></div>
    <div class="abs" role="img" aria-label="Video door station mounted on a pale wall" style="left:860px;top:0;width:186px;height:86px;background:linear-gradient(90deg,#d7d9db,var(--photo-light) 40%,#cfd2d4)"></div>

    <h1 class="abs page-title" style="left:548px;top:48px">Intercom</h1>

    <div class="abs body-copy" style="left:548px;top:94px;width:302px">
      <p>A Harrowgate Locks and Grilles Intercom system is a great addition to any home. Giving you the ability to communicate with visitors to your home at your front door or even at your front gate. In conjunction with the use of an electric strike you can hit the door release button on the intercom and let them in from where you stand in the home. Maybe even better still, decide to not let them in.</p>
      <p>With the video intercom option your visitor will be displayed automatically and you can view who it is without them even knowing you are there.</p>
    </div>

    <div class="abs product-photo" role="img" aria-label="Colour monitor with door station" style="left:548px;top:186px;width:77px;height:44px"></div>
    <h2 class="abs product-name" style="left:637px;top:182px">KA Colour Video Intercom</h2>
    <p class="abs product-copy" style="left:637px;top:195px;width:213px">Superior quality, touch button control and door release. This sleek glass face 7" screen intercom is just what you need to visually see and communicate with who is at the front gate or door. With the add on addition of a extra monitor makes it perfect for two story homes with the extra station up stairs.</p>
    <div class="abs divider" style="left:548px;top:244px;width:302px"></div>

    <div class="abs product-photo" role="img" aria-label="Touch screen monitor with door station" style="left:548px;top:266px;width:77px;height:40px"></div>
    <h2 class="abs product-name" style="left:637px;top:257px">KB Colour Video Intercom</h2>
    <p class="abs product-copy" style="left:637px;top:270px;width:213px">All the smarts built into a compact, modern designed glass face monitor. This unit has touch screen control, inter home communication between monitors and a build in handset for minimal disturbance when required. With maximums of 4 door stations and 8 Monitors, this system is perfect for the homes with multiple entry points and when multiple room monitors are required.</p>
    <div class="abs divider" style="left:548px;top:329px;width:302px"></div>

    <div class="abs product-photo" role="img" aria-label="Audio door station and handset" style="left:566px;top:337px;width:46px;height:53px;background:linear-gradient(135deg,#eceeef,#9ea3a7)"></div>
    <h2 class="abs product-name" style="left:637px;top:339px">Audio Only Intercom</h2>
    <p class="abs product-copy" style="left:637px;top:352px;width:213px">Whether it's to help fit within the budget, and you just don't have the requirement of having to see who is at the door, this no fuss, single purpose audio only intercom&nbsp; is that handy addition to the living area.</p>

    <h3 class="abs section-label" style="left:876px;top:96px">POPULAR UPGRADES</h3>
    <div class="abs tile upgrade-tile" style="left:876px;top:121px;width:153px;height:65px"><div class="tile-photo" role="img" aria-label="Stainless steel door station"></div><span class="tile-label">Upgrade to flush mount<br>stainless steel door station</span></div>
    <div class="abs tile upgrade-tile" style="left:876px;top:192px;width:153px;height:66px"><div class="tile-photo" role="img" aria-label="Electric door strike"></div><span class="tile-label">Extend Intercom wiring<br>to property font gate</span></div>
    <div class="abs tile upgrade-tile" style="left:876px;top:263px;width:153px;height:65px"><div class="tile-photo" role="img" aria-label="Additional video monitor" style="height:30px"></div><span class="tile-label">Additional monitor<br>installed. (Video Only)</span></div>
  </section>

</main>
</body>
</html>
```